Information One Page for Email

I am looking for a informative attachment I can send with an introductive email for Meridale Slab Works. Something I can also Mail.

Meridale Slab Works is the leader in Rebar Post Tension Cable Placement and Post Tension Cable repair. Outside of cable placement and repair we do concrete repair, Parking Garage restoration and
Updates

Content

Post Tension Repair and Concrete Restoration
Post-tensioning is a revolutionary method in concrete construction that enhances the strength and durability of structures. However, like all construction ele-ments, post-tension cables can experience wear and damage over time. Ensuring timely and effective repair is crucial for maintaining the safety and integrity of your building.
Why Post-Tension Cable Repair is Essential
1. **Structural Integrity**: Damaged or deteriorated cables can compromise the structural integrity of your building, leading to safety hazards and potential structural failures.
2. **Extended Lifespan**: Regular maintenance and repair of post-tension cables extend the lifespan of your structure, ensuring it remains safe and function-al for years to come.
3. **Cost-Effective**: Addressing cable issues early on prevents more severe damage and costly repairs down the line.
Common Signs of Post-Tension Cable Issues
- Cracks in concrete surfaces
- Unusual noises or popping sounds
- Visible cable ends or broken strands
- Water leakage through cracks
Our Repair Process
1. **Inspection and Assessment**: Our team conducts a thorough inspection to identify the extent of the damage and determine the appropriate repair meth-ods.
2. **Cable Repair or Replacement**: Depending on the severity, we either re-pair the existing cables or replace them with new ones to restore full functional-ity.
3. **Sealing and Protection**: After repairing, we seal the affected areas to protect against moisture and future damage.
4. **Quality Assurance**: We perform rigorous quality checks to ensure the repairs meet industry standards and the structure is safe for use.
Why Choose Us
- **Expertise and Experience**: With years of experience in post-tension cable repair, our team is skilled in handling even the most complex repairs efficiently and effectively.
- **Advanced Technology**: We use the latest technology and materials to ensure durable and long-lasting repairs.
- **Customer Satisfaction**: Our commitment to quality and customer satisfaction sets us apart. We work closely with our clients to ensure their needs are met and expectations exceeded.
Contact Us
If you suspect issues with your post-tension cables or need a routine inspection, don't hesitate to contact us. Our experts are ready to provide the best solutions to keep your structures safe and secure.
Ensure the safety and longevity of your building with our professional post-tension cable repair services. Trust us to deliver quality and reliability every time.

```html
<!DOCTYPE html>
<html lang="en">
<head>
<meta charset="utf-8">
<title>Meridale Slab Works – Post Tension Repair and Concrete Restoration</title>
<link rel="stylesheet" href="https://fonts.googleapis.com/css2?family=Poppins:wght@300;400;500;600;700;800&display=swap">
<style>
  :root {
    --green: #0a6a3b;
    --green-dark: #0b4a2a;
    --green-bright: #2f8a1c;
    --ink: #1b1b1b;
    --grey-icon: #8c8c8c;
    --line: #555555;
    --rule: #cfcfcf;
    --paper: #ffffff;
  }
  * { margin: 0; padding: 0; box-sizing: border-box; }
  html, body { width: 800px; height: 1200px; overflow: hidden; }
  body { background: var(--paper); font-family: "Poppins", sans-serif; color: var(--ink); position: relative; }
  .abs { position: absolute; }

  .connectors { position: absolute; left: 0; top: 0; }

  .brand { left: 61px; top: 62px; display: flex; align-items: center; gap: 10px; }
  .brand-mark { width: 18px; height: 18px; background: var(--green); }
  .brand-name { font-weight: 700; font-size: 27px; color: var(--green); line-height: 1; }

  .headline { left: 61px; top: 144px; font-size: 39px; line-height: 40px; font-weight: 800; letter-spacing: -0.5px; }
  .headline .accent { color: var(--green); }
  .headline .light { font-weight: 400; }

  .hero-photo { left: 427px; top: 58px; width: 306px; height: 251px;
    background: linear-gradient(160deg, #d9d9d7 0%, #b8b6b0 45%, #8f8c84 100%); }

  .intro { left: 61px; top: 343px; width: 672px; height: 94px; background: var(--green); color: #fff;
    font-size: 12px; line-height: 14px; padding: 20px 30px; text-align: justify; font-weight: 400; }

  .section-title { font-size: 14.5px; line-height: 16px; font-weight: 700; color: var(--green); text-transform: uppercase; }

  .benefit { left: 61px; width: 320px; display: flex; gap: 10px; }
  .benefit .icon { flex: none; width: 41px; height: 41px; border-radius: 50%; background: var(--grey-icon);
    display: flex; align-items: center; justify-content: center; margin-top: 1px; }
  .benefit h3 { font-size: 13.5px; font-weight: 600; line-height: 18px; margin-bottom: 1px; }
  .benefit p { font-size: 10.5px; line-height: 12.5px; font-weight: 400; }

  .sign { display: flex; gap: 6px; font-size: 10.5px; line-height: 12.5px; font-weight: 500; width: 150px; }
  .tick { flex: none; width: 12px; height: 12px; margin-top: 0.5px; }

  .site-photo { top: 580px; width: 150px; height: 129px; border: 1px solid #777; }
  .site-photo.one { left: 426px; background: linear-gradient(180deg, #b9b4a6 0%, #8a8272 55%, #6d6a62 100%); }
  .site-photo.two { left: 592px; background: linear-gradient(180deg, #a9a59c 0%, #7f7b73 50%, #5c5a55 100%); }

  .divider-title { left: 61px; width: 680px; display: flex; align-items: center; gap: 10px; }
  .divider-title::before, .divider-title::after { content: ""; flex: 1; height: 1px; background: var(--rule); }
  .divider-title span { font-weight: 700; color: var(--green); font-size: 15px; }

  .step { top: 775px; width: 154px; height: 162px; color: #fff; text-align: center; padding: 30px 12px 0;
    background: linear-gradient(120deg, var(--green-bright) 0%, #15642a 50%, var(--green-dark) 100%); }
  .step::after { content: ""; position: absolute; right: -10px; top: 71px; border-left: 10px solid #0d4f2b;
    border-top: 10px solid transparent; border-bottom: 10px solid transparent; }
  .step.last::after { display: none; }
  .step h3 { font-size: 12.5px; line-height: 14px; font-weight: 700; margin-bottom: 4px; }
  .step p { font-size: 10.5px; line-height: 14px; font-weight: 300; }
  .step-badge { position: absolute; left: 50%; top: -22px; margin-left: -22px; width: 44px; height: 44px; border-radius: 50%;
    background: var(--grey-icon); border: 3px solid #fff; display: flex; align-items: center; justify-content: center; }

  .reason { top: 983px; display: flex; gap: 8px; }
  .reason h3 { font-size: 13.5px; line-height: 17px; font-weight: 600; margin-bottom: 1px; }
  .reason p { font-size: 10.5px; line-height: 12.4px; }
  .reason .tick { width: 13px; height: 13px; margin-top: 2px; }

  .rule-h { left: 61px; top: 1073px; width: 680px; height: 1px; background: var(--rule); }
  .rule-v { left: 436px; top: 1096px; width: 1px; height: 78px; background: #999; }

  .contact-copy { left: 61px; top: 1093px; width: 340px; }
  .contact-copy p { font-size: 10.5px; line-height: 12.4px; font-weight: 500; margin-top: 3px; }
  .contact-copy p + p { margin-top: 9px; font-weight: 400; }

  .contact-list { left: 475px; top: 1094px; list-style: none; }
  .contact-list li { display: flex; align-items: center; gap: 7px; font-size: 12px; line-height: 20px; font-weight: 500; }
  .contact-list svg { width: 11px; height: 11px; flex: none; }

  .footer-band { left: 0; top: 1190px; width: 800px; height: 10px; background: var(--green-dark); }
</style>
</head>
<body>

<svg class="connectors" width="800" height="1200" viewBox="0 0 800 1200" aria-hidden="true">
  <g fill="none" stroke="var(--line)" stroke-width="1.2">
    <polyline points="592,40 751,40 751,437 800,437"/>
    <polyline points="64,324 769,324 769,452 800,452"/>
    <path d="M595,36 v8 M67,320 v8"/>
  </g>
</svg>

<div class="abs brand">
  <span class="brand-mark"></span>
  <span class="brand-name">Meridale Slab Works</span>
</div>

<h1 class="abs headline">
  <span class="accent">POST TENSION</span><br>
  REPAIR AND<br>
  CONCRETE<br>
  <span class="light">RESTORATION</span>
</h1>

<div class="abs hero-photo" role="img" aria-label="Photo of a multi-storey concrete building with shored balcony slabs under repair"></div>

<div class="abs intro">
  Post-tensioning is a revolutionary method in concrete construction that enhances the strength and durability of structures. However, like all construction ele-ments, post-tension cables can experience wear and damage over time. Ensuring timely and effective repair is crucial for maintaining the safety and integrity of your building.
</div>

<h2 class="abs section-title" style="left:61px; top:455px;">Why Post-Tension Cable<br>Repair is Essential</h2>

<div class="abs benefit" style="top:503px;">
  <div class="icon"><svg width="22" height="22" viewBox="0 0 22 22" fill="none" stroke="#fff" stroke-width="1.3"><path d="M2 6h18M2 11h18M2 16h18M4 6l4 10 4-10 4 10 4-10"/></svg></div>
  <div><h3>Structural Integrity</h3><p>Damaged or deteriorated cables can compromise the structural integrity of your building, leading to safety hazards and potential structural failures.</p></div>
</div>

<div class="abs benefit" style="top:580px;">
  <div class="icon"><svg width="22" height="22" viewBox="0 0 22 22" fill="none" stroke="#fff" stroke-width="1.3"><rect x="6" y="4" width="10" height="14" rx="1"/><circle cx="11" cy="13" r="3"/><path d="M11 11.5v1.5h1.2M3 8a8 8 0 0 1 3-4M19 14a8 8 0 0 1-3 4"/></svg></div>
  <div><h3>Extended Lifespan</h3><p>Regular maintenance and repair of post-tension cables extend the lifespan of your structure, ensuring it remains safe and function-al for years to come.</p></div>
</div>

<div class="abs benefit" style="top:666px;">
  <div class="icon"><svg width="22" height="22" viewBox="0 0 22 22" fill="#fff"><rect x="4" y="15" width="3" height="4"/><rect x="9" y="12" width="3" height="7"/><rect x="14" y="9" width="3" height="10"/><path d="M4 11l6-4 3 2 5-5" fill="none" stroke="#fff" stroke-width="1.3"/><circle cx="6" cy="5" r="2.5" fill="none" stroke="#fff" stroke-width="1.1"/></svg></div>
  <div><h3>Cost-Effective</h3><p>Addressing cable issues early on prevents more severe damage and costly repairs down the line.</p></div>
</div>

<h2 class="abs section-title" style="left:420px; top:455px;">Common Signs of Post-Tension<br>Cable Issues</h2>

<svg width="0" height="0" style="position:absolute"><defs>
  <symbol id="tick" viewBox="0 0 12 12"><circle cx="6" cy="6" r="6" fill="#0b4a2a"/><path d="M3.3 6.2l1.8 1.8 3.6-3.8" fill="none" stroke="#fff" stroke-width="1.4"/></symbol>
</defs></svg>

<div class="abs sign" style="left:420px; top:502px;"><svg class="tick"><use href="#tick"/></svg><span>Cracks in concrete surfaces</span></div>
<div class="abs sign" style="left:594px; top:502px;"><svg class="tick"><use href="#tick"/></svg><span>Visible cable ends or broken strands</span></div>
<div class="abs sign" style="left:420px; top:541px;"><svg class="tick"><use href="#tick"/></svg><span>Unusual noises or popping sounds</span></div>
<div class="abs sign" style="left:594px; top:541px;"><svg class="tick"><use href="#tick"/></svg><span>Water leakage through cracks</span></div>

<div class="abs site-photo one" role="img" aria-label="Photo of a worker breaking out a damaged concrete balcony slab"></div>
<div class="abs site-photo two" role="img" aria-label="Photo of crew members working on post-tension cables on a slab deck"></div>

<div class="abs divider-title" style="top:727px;"><span>OUR REPAIR PROCESS</span></div>

<div class="abs step" style="left:61px;">
  <div class="step-badge"><svg width="20" height="20" viewBox="0 0 20 20" fill="none" stroke="#fff" stroke-width="1.3"><rect x="4" y="3" width="11" height="14" rx="1"/><path d="M7 7h5M7 10h3"/><circle cx="12" cy="12" r="2.5"/><path d="M14 14l3 3"/></svg></div>
  <h3>Inspection and Assessment</h3>
  <p>Our team conducts a thorough inspection to identify the extent of the damage and determine the appropriate repair meth-ods.</p>
</div>
<div class="abs step" style="left:235px;">
  <div class="step-badge"><svg width="20" height="20" viewBox="0 0 20 20" fill="none" stroke="#fff" stroke-width="1.5"><path d="M4 9a6 6 0 0 1 11-3M16 11a6 6 0 0 1-11 3"/><path d="M15 2v4h-4M5 18v-4h4"/></svg></div>
  <h3>Cable Repair or Replacement</h3>
  <p>Depending on the severity, we either re-pair the existing cables or replace them with new ones to restore full functional-ity.</p>
</div>
<div class="abs step" style="left:410px;">
  <div class="step-badge"><svg width="20" height="20" viewBox="0 0 20 20" fill="#fff"><circle cx="9" cy="9" r="6"/><circle cx="9" cy="9" r="2.2" fill="#8c8c8c"/><circle cx="14.5" cy="14.5" r="3.5" stroke="#8c8c8c" stroke-width="1"/></svg></div>
  <h3>Sealing and Protection</h3>
  <p>After repairing, we seal the affected areas to protect against moisture and future damage.</p>
</div>
<div class="abs step last" style="left:586px;">
  <div class="step-badge"><svg width="20" height="20" viewBox="0 0 20 20" fill="none" stroke="#fff" stroke-width="1.3"><circle cx="10" cy="10" r="7.5"/><circle cx="10" cy="10" r="5"/><path d="M7.8 10l1.6 1.6 3-3"/></svg></div>
  <h3>Quality Assurance</h3>
  <p>We perform rigorous quality checks to ensure the repairs meet industry standards and the structure is safe for use.</p>
</div>

<div class="abs divider-title" style="top:950px;"><span>Why Choose Us</span></div>

<div class="abs reason" style="left:58px; width:200px;">
  <svg class="tick"><use href="#tick"/></svg>
  <div><h3>Expertise and Experience</h3><p>With years of experience in post-tension cable repair, our team is skilled in handling even the most complex repairs efficiently and effectively.</p></div>
</div>
<div class="abs reason" style="left:307px; width:200px;">
  <svg class="tick"><use href="#tick"/></svg>
  <div><h3>Advanced Technology</h3><p>We use the latest technology and materials to ensure durable and long-lasting repairs.</p></div>
</div>
<div class="abs reason" style="left:547px; width:200px;">
  <svg class="tick"><use href="#tick"/></svg>
  <div><h3>Structural Integrity</h3><p>Our commitment to quality and customer satisfaction sets us apart. We work closely with our clients to ensure their needs are met and expectations exceeded.</p></div>
</div>

<div class="abs rule-h"></div>

<div class="abs contact-copy">
  <h2 class="section-title" style="font-size:15px;">Contact Us</h2>
  <p>If you suspect issues with your post-tension cables or need a routine inspection, don't hesitate to contact us.</p>
  <p>Our experts are ready to provide the best solutions to keep your structures safe and secure.</p>
</div>

<div class="abs rule-v"></div>

<ul class="abs contact-list">
  <li><svg viewBox="0 0 12 12" fill="var(--green)"><path d="M2.5 1l2 2.2-1 1.3a6.5 6.5 0 0 0 3.9 3.9l1.3-1 2.2 2L10 11C5 11 1 7 1 2z"/></svg>(555) 014-2270</li>
  <li><svg viewBox="0 0 12 12" fill="var(--green)"><path d="M1 3h10v6H1z"/><path d="M1 3l5 3.5L11 3" fill="none" stroke="#fff" stroke-width="0.9"/></svg>info@meridaleslabworks.com</li>
  <li><svg viewBox="0 0 12 12" fill="var(--green)"><path d="M6 0.5a4 4 0 0 1 4 4c0 3-4 7-4 7s-4-4-4-7a4 4 0 0 1 4-4z"/><circle cx="6" cy="4.5" r="1.5" fill="#fff"/></svg>480 Kestrel Ridge Road Ashford Bay, FL 30019</li>
  <li><svg viewBox="0 0 12 12" fill="none" stroke="var(--green)" stroke-width="1"><circle cx="6" cy="6" r="5"/><ellipse cx="6" cy="6" rx="2.2" ry="5"/><path d="M1 6h10"/></svg>www.meridaleslabworks.com</li>
</ul>

<div class="abs footer-band"></div>

</body>
</html>
```